Business card design needed

Card needs to say

Maren Heathwold
Investor - Solutions - Development

My business is in property deals. I would like the words above to be on the card. I have attached a logo for you to copy/recreate.
On the back you could list the following:

Creative property solutions

Thankyou, Maren

Target Market(s)

people wanting to get into the property market, desperate sellers, Mums & Dads wanting to help their kids to purchase a property. People who want to create wealth. People who are stuck and need a solution.

Industry/Entity Type

Business

Contact Information for Business Card

T: 0431 274 506
F: (07) 3842 1739
E: maren47@vbx-mail.com.au

Requirements
Must have
• Simple and effective.
Look like I am here to help
Should not have
• Should not look like a realestate agent

```html
<!DOCTYPE html>
<html lang="en">
<head>
<meta charset="utf-8">
<title>Maren Heathwold – Business Cards</title>
<link rel="stylesheet" href="https://fonts.googleapis.com/css2?family=Quicksand:wght@400;500&display=swap">
<style>
  :root {
    --page-bg: #ffffff;
    --card-top: #ffffff;
    --card-bottom: #dcdcdc;
    --band: #5a7b8d;
    --band-edge: #9b9b9b;
    --name-ink: #555555;
    --tagline-ink: #6a6a6a;
    --mark-ink: #8ea6b4;
    --contact-ink: #ffffff;
  }
  * { box-sizing: border-box; margin: 0; padding: 0; }
  html, body {
    width: 1200px; height: 657px; overflow: hidden;
    background: var(--page-bg);
    font-family: "Quicksand", sans-serif;
  }
  .canvas { position: relative; width: 1200px; height: 657px; }

  .card {
    position: absolute;
    overflow: hidden;
    background: linear-gradient(to bottom, var(--card-top) 0%, var(--card-top) 30%, var(--card-bottom) 100%);
    text-align: center;
  }
  .card--landscape { left: 43px; top: 116px; width: 612px; height: 336px; }
  .card--portrait  { left: 766px; top: 46px; width: 352px; height: 577px; }

  .brand-mark {
    position: absolute; left: 0; right: 0;
    display: flex; align-items: center; justify-content: center; gap: 12px;
    color: var(--mark-ink); font-weight: 500;
  }
  .brand-mark__dot { border-radius: 50%; background: var(--mark-ink); }
  .card--landscape .brand-mark { top: 92px; font-size: 28px; }
  .card--landscape .brand-mark__dot { width: 22px; height: 22px; }
  .card--portrait .brand-mark { top: 150px; font-size: 28px; }
  .card--portrait .brand-mark__dot { width: 22px; height: 22px; }

  .holder-name { position: absolute; left: 0; right: 0; color: var(--name-ink); font-weight: 400; letter-spacing: 0.5px; }
  .tagline { position: absolute; left: 0; right: 0; color: var(--tagline-ink); font-weight: 400; }

  .card--landscape .holder-name { top: 168px; font-size: 52px; }
  .card--landscape .tagline { top: 234px; font-size: 23px; }
  .card--portrait .holder-name { top: 290px; font-size: 38px; }
  .card--portrait .tagline { top: 338px; font-size: 18px; }

  .band { position: absolute; left: 0; bottom: 0; width: 100%; }
  .contact {
    position: absolute; left: 0; right: 0;
    color: var(--contact-ink); font-weight: 400;
  }
  .card--landscape .contact { bottom: 6px; font-size: 19px; white-space: nowrap; }
  .card--portrait .contact { top: 462px; font-size: 21px; line-height: 30px; }
</style>
</head>
<body>
<main class="canvas">

  <section class="card card--landscape" aria-label="Business card, landscape">
    <div class="brand-mark"><span class="brand-mark__dot"></span><span>Homeward Lane</span></div>
    <h1 class="holder-name">Maren Heathwold</h1>
    <p class="tagline">Investor – Solutions – Development</p>
    <svg class="band" width="612" height="46" viewBox="0 0 612 46" aria-hidden="true">
      <path d="M0 11 Q306 -3 612 11 L612 46 L0 46 Z" fill="var(--band-edge)"/>
      <path d="M0 16 Q306 2 612 16 L612 46 L0 46 Z" fill="var(--band)"/>
    </svg>
    <p class="contact">T: 0431 274 506 F: (07) 3842 1739 E: maren47@vbx-mail.com.au</p>
  </section>

  <section class="card card--portrait" aria-label="Business card, portrait">
    <div class="brand-mark"><span class="brand-mark__dot"></span><span>Homeward Lane</span></div>
    <h2 class="holder-name">Maren Heathwold</h2>
    <p class="tagline">Investor – Solutions – Development</p>
    <svg class="band" width="352" height="140" viewBox="0 0 352 140" aria-hidden="true">
      <path d="M0 14 Q176 -6 352 14 L352 140 L0 140 Z" fill="var(--band-edge)"/>
      <path d="M0 19 Q176 -1 352 19 L352 140 L0 140 Z" fill="var(--band)"/>
    </svg>
    <p class="contact">T: 0431 274 506<br>F: (07) 3842 1739<br>E: maren47@vbx-mail.com.au</p>
  </section>

</main>
</body>
</html>
```